Harborview Estates Business Card for Apartment Buildings

Create business cards for resident managers who run apartment buildings. The audience is the public who are searching for apartment rentals, and current residents who live at the apartment building. Key design element will be incorporating the company logo, however, the logo cannot dominate. The building name and manager name are more important than the logo. Current business card design leaves little room for copy, so we may need to reduce the size on the current card to allow for more space for copy.

Target Market(s)

Adults 18-65 years of age, who are looking for an apartment rental, plus current residents who live at our apartment buildings.

Industry/Entity Type

Property Management

Contact Information for Business Card

A major design element will be use of the company logo. Important property and manager contact information must be part of the design. The size of the logo will need to be reduced to make room for building and manager contact copy.

Font styles to use
Sans Serif

Colors
3176b5
000000
959595
ffffff

Requirements
Must have
• 1) Incorporate the company logo.
• 2) Use the company colors (dark blue, black/grey, over white).
• 3) FEATURE THE BUILDING NAME
• 4) FEATURE THE MANAGER NAME
• 5) The company name is less important than BUILDING and MANAGER
• 6) Manager contact information
• **SEE ATTACHED CREATIVE BRIEF**
Nice to have
• 1) Back of card logo watermark
• 2) Ability to write notes on back of carfd
Should not have
• Avoid letting the company logo dominate the card, the building name and manager are more important than the company logo.

```html
<!DOCTYPE html>
<html lang="en">
<head>
<meta charset="utf-8">
<title>Harborview Estates – Resident Manager Card</title>
<link href="https://fonts.googleapis.com/css2?family=Roboto+Condensed:wght@400;700&family=Roboto:wght@400;500&display=swap" rel="stylesheet">
<style>
  :root {
    --stage: #2b2b2b;
    --brand-blue: #126aa9;
    --watermark: rgba(255, 255, 255, .09);
    --watermark-text: rgba(255, 255, 255, .13);
    --paper: #f1f1f1;
    --divider: #555555;
    --white: #ffffff;
  }
  html, body {
    margin: 0;
    width: 1200px;
    height: 960px;
    overflow: hidden;
    background: var(--stage);
  }
  .canvas { position: relative; width: 1200px; height: 960px; }

  .card {
    position: absolute;
    left: 320px;
    width: 600px;
    height: 342px;
    overflow: hidden;
  }

  /* Back of card */
  .card-back { top: 108px; background: var(--brand-blue); }
  .watermark {
    position: absolute;
    left: 126px; top: 12px;
    width: 320px; height: 320px;
    border-radius: 50%;
    background: var(--watermark);
    display: flex;
    align-items: center;
    justify-content: center;
  }
  .watermark-name {
    text-align: center;
    font: 700 34px/1.1 "Roboto Condensed", sans-serif;
    letter-spacing: 1px;
    color: var(--watermark-text);
    text-transform: uppercase;
  }

  /* Front of card */
  .card-front { top: 493px; background: var(--paper); }
  .card-front .panel { position: absolute; left: 0; top: 0; }
  .brand {
    position: absolute;
    left: 42px; top: 152px;
    display: flex; align-items: center; gap: 10px;
  }
  .brand-dot {
    width: 26px; height: 26px; border-radius: 50%;
    background: var(--brand-blue);
    flex: none;
  }
  .brand-name {
    font: 700 21px/1 "Roboto Condensed", sans-serif;
    color: var(--brand-blue);
    text-transform: uppercase;
    letter-spacing: .3px;
    white-space: nowrap;
  }

  .details {
    position: absolute;
    left: 351px; top: 61px;
    color: var(--white);
    font-family: "Roboto", sans-serif;
  }
  .manager-name { margin: 0; font: 700 23px/1.1 "Roboto Condensed", sans-serif; }
  .manager-title { margin: 3px 0 0; font: 500 15px/1.2 "Roboto", sans-serif; }
  .building-name { margin: 24px 0 0; font: 700 14.5px/1.2 "Roboto", sans-serif; }
  .address { margin: 2px 0 0; font-size: 14px; line-height: 19px; }
  .contacts { list-style: none; margin: 8px 0 0; padding: 0; font-size: 14px; line-height: 19px; }
  .contacts li { display: flex; align-items: center; gap: 8px; }
  .contacts svg { width: 13px; height: 13px; fill: var(--white); flex: none; }
</style>
</head>
<body>
<div class="canvas">

  <section class="card card-back" aria-label="Back of card">
    <div class="watermark">
      <div class="watermark-name">Harborview<br>Estates</div>
    </div>
  </section>

  <section class="card card-front" aria-label="Front of card">
    <svg class="panel" width="600" height="342" viewBox="0 0 600 342">
      <path d="M313 0 V70 L323 85 L313 100 V342 H600 V0 Z" fill="#126aa9"/>
      <path d="M310 0 V70 L320 85 L310 100 V342" fill="none" stroke="#555555" stroke-width="3"/>
    </svg>

    <div class="brand">
      <span class="brand-dot"></span>
      <span class="brand-name">Harborview Estates</span>
    </div>

    <div class="details">
      <h1 class="manager-name">Marisol Delgado</h1>
      <p class="manager-title">Resident Manager</p>
      <p class="building-name">Linden Court Apartments</p>
      <p class="address">2450 Cedar Avenue<br>Bayside, CA 90210</p>
      <ul class="contacts">
        <li><svg viewBox="0 0 24 24"><path d="M6.6 10.8a15 15 0 0 0 6.6 6.6l2.2-2.2c.3-.3.7-.4 1-.2 1.1.4 2.3.6 3.6.6.6 0 1 .4 1 1V20c0 .6-.4 1-1 1A17 17 0 0 1 3 4c0-.6.4-1 1-1h3.5c.6 0 1 .4 1 1 0 1.3.2 2.5.6 3.6.1.3 0 .7-.2 1z"/></svg>555-201-4410</li>
        <li><svg viewBox="0 0 24 24"><path d="M7 1h10a2 2 0 0 1 2 2v18a2 2 0 0 1-2 2H7a2 2 0 0 1-2-2V3a2 2 0 0 1 2-2zm0 3v14h10V4zm5 15.5a1.2 1.2 0 1 0 0 2.4 1.2 1.2 0 0 0 0-2.4z"/></svg>555-384-7726</li>
        <li><svg viewBox="0 0 24 24"><path d="M6 2h12v5H6zM3 8h18a2 2 0 0 1 2 2v7h-4v5H5v-5H1v-7a2 2 0 0 1 2-2zm4 8v4h10v-4z"/></svg>555-612-3090</li>
        <li><svg viewBox="0 0 24 24"><path d="M2 5h20v14H2zm2 2v.5l8 5 8-5V7z"/></svg>marisol@harborviewest.com</li>
        <li><svg viewBox="0 0 24 24"><path d="M12 2a10 10 0 1 0 0 20 10 10 0 0 0 0-20zm-1 17.9A8 8 0 0 1 4.1 10L9 15v1a2 2 0 0 0 2 2zm6.9-2.5A2 2 0 0 0 16 16h-1v-3a1 1 0 0 0-1-1H8v-2h2a1 1 0 0 0 1-1V7h2a2 2 0 0 0 2-2v-.4a8 8 0 0 1 2.9 12.8z"/></svg>www.harborviewest.com</li>
      </ul>
    </div>
  </section>

</div>
</body>
</html>
```